Federal Government Proposal Development Consulting company needs a website designed and coded

I am looking for someone to design (using an existing logo, color palette, and text fonts) and code a wordpress-based website for a Proposal Development consulting company. I have full copy for all site pages and suggestions for images/ graphics and a few example design templates to go from.

One note, from a color perspective - I included a mockup of a business card to highlight a color scheme that I tend to like - if you look at the back of the business card, the blend of the grey, blue, with the neon green highlight as a separator really seems to pop. Just a thought as you are designing the page.

I would like to see 2-3 potential design layouts, and I will select one to move forward with. Then, I would like the site to be coded for WordPress (I can provide a login to my wordpress site). I would like 1 opportunity to review the coded site and make any final tweaks.

```html
<!DOCTYPE html>
<html lang="en">
<head>
<meta charset="utf-8">
<title>Northgate Bid Partners</title>
<link href="https://fonts.googleapis.com/css2?family=Della+Respira&family=Raleway:wght@400;500;600;700&family=Roboto:ital,wght@0,400;0,500;0,700;1,400&display=swap" rel="stylesheet">
<style>
:root{
  --blue:#1544b8;
  --green:#1ff0bd;
  --navy:#070b2c;
  --ink:#1d1d1f;
  --text:#555;
  --pale:#e9efff;
  --grey:#ececec;
  --card:#f2f2f2;
}
*{box-sizing:border-box;margin:0;padding:0}
html,body{width:1200px;height:4950px;overflow:hidden}
body{position:relative;font-family:"Raleway",sans-serif;color:var(--ink);background:#fff}
section,header,footer{position:absolute;left:0;width:1200px}
.btn{position:absolute;display:flex;align-items:center;justify-content:center;gap:10px;border-radius:22px;font:700 15px "Raleway",sans-serif;letter-spacing:.3px}
.btn .dot{width:14px;height:14px;border-radius:50%;display:inline-flex}
.btn-green{background:var(--green);color:#0b1b3a}
.btn-green .dot{background:#0b1b3a}
.btn-blue{background:var(--blue);color:#fff}
.btn-blue .dot{background:#fff}
.h2{position:absolute;left:0;width:1200px;text-align:center;font-family:"Della Respira",serif;font-size:33px;color:var(--ink)}

/* header */
.site-header{top:0;height:97px;background:#fff;z-index:3}
.brand{position:absolute;left:112px;top:0;width:258px;height:120px;background:#fff;display:flex;align-items:center;justify-content:center;box-shadow:0 2px 4px rgba(0,0,0,.08)}
.brand-name{font-family:"Raleway",sans-serif;font-weight:600;font-size:21px;color:#2b2f3a;white-space:nowrap}
.nav{position:absolute;left:400px;top:36px;display:flex;gap:32px;font-size:17px;color:#333}
.login{left:943px;top:28px;width:144px;height:40px}

/* hero */
.hero{top:97px;height:653px}
.hero-photo{position:absolute;inset:0;background:linear-gradient(100deg,#101a2c 0%,#233047 35%,#2a4c87 60%,#1c3c7a 80%,#0f1f42 100%)}
.hero-title{position:absolute;left:0;width:746px;top:215px;text-align:center;font-family:"Della Respira",serif;font-size:55px;color:#fff}
.hero-sub{position:absolute;left:130px;width:486px;top:302px;text-align:center;font-size:17px;line-height:29px;color:#fff}
.hero .btn{left:288px;top:385px;width:170px;height:40px}

/* what we do */
.what{top:750px;height:967px}
.what .h2{top:82px}
.lead{position:absolute;left:158px;width:884px;text-align:justify;text-align-last:center;font-size:15.5px;line-height:31px;color:var(--text)}
.rule{position:absolute;left:112px;width:975px;top:455px;height:1px;background:#ddd}
.feature{position:absolute;top:527px;width:320px;height:353px;background:#fff;border-radius:22px;box-shadow:0 4px 22px rgba(0,0,0,.12);text-align:center;overflow:hidden}
.feature .ico{width:110px;height:110px;border-radius:50%;background:var(--blue);margin:23px auto 0;display:flex;align-items:center;justify-content:center}
.feature h3{font-family:"Della Respira",serif;font-weight:400;font-size:19px;margin-top:27px;color:#333}
.feature p{font-family:"Roboto",sans-serif;font-size:12.5px;line-height:23px;color:#777;width:265px;margin:8px auto 0}
.feature .more{font-family:"Roboto",sans-serif;font-weight:700;font-size:13px;color:var(--blue);margin-top:16px;display:flex;justify-content:center;align-items:center;gap:8px}
.feature .more i{width:12px;height:12px;border-radius:50%;background:var(--blue);display:inline-block}
.feature.active::after{content:"";position:absolute;left:20px;right:20px;bottom:0;height:4px;background:var(--green);border-radius:2px}

/* who */
.who{top:1717px;height:591px;background:var(--pale)}
.who-photo{position:absolute;left:124px;top:82px;width:424px;height:424px;border-radius:50%;border:6px solid #fff;background:radial-gradient(circle at 60% 60%,#c9d33a 0%,#6b7a5a 30%,#4b5d6c 60%,#2d3b4c 100%);box-shadow:0 6px 20px rgba(0,0,0,.2)}
.who-title{position:absolute;left:597px;top:78px;font-family:"Della Respira",serif;font-size:33px}
.who-text{position:absolute;left:597px;width:480px;font-size:15px;line-height:31px;color:#333;text-align:justify}
.who .btn{left:597px;top:466px;width:169px;height:40px}

/* services */
.services{top:2308px;height:562px}
.services .h2{top:82px}
.svc{position:absolute;top:165px;width:236px;height:307px;background:var(--card);text-align:center}
.svc.active{background:#fff;box-shadow:0 4px 16px rgba(0,0,0,.12)}
.svc.active::after{content:"";position:absolute;left:0;right:0;bottom:0;height:4px;background:var(--green);border-radius:2px}
.svc .ico{width:88px;height:88px;border-radius:50%;background:var(--blue);margin:19px auto 0;display:flex;align-items:center;justify-content:center}
.svc.active .ico{background:var(--green)}
.svc h3{font-weight:500;font-size:15.5px;margin-top:23px;color:#222}
.svc p{font-family:"Roboto",sans-serif;font-size:13.5px;line-height:25px;color:#777;width:205px;margin:10px auto 0}
.arrow{position:absolute;top:307px;width:38px;height:38px;border-radius:50%;border:1.5px solid #bbb;display:flex;align-items:center;justify-content:center}

/* sme */
.sme{top:2870px;height:563px;background:linear-gradient(180deg,#1245c0,#0c3bb0)}
.sme .h2{top:60px;color:#fff}
.topic{position:absolute;top:162px;width:200px;text-align:center;color:#fff;font-size:15.5px;line-height:20px}
.topic .pic{width:176px;height:176px;border-radius:50%;border:2px solid #fff;margin:0 auto 20px}
.sme .btn{left:515px;top:450px;width:170px;height:40px}

/* testimonials */
.testi{top:3433px;height:505px}
.testi .h2{top:82px}
.quote{position:absolute;top:150px;width:313px;height:267px;background:#fff;box-shadow:0 3px 16px rgba(0,0,0,.1)}
.quote .avatar{position:absolute;left:20px;top:26px;width:48px;height:48px;border-radius:50%;background:linear-gradient(#c7ccd4,#8e96a3)}
.quote .name{position:absolute;left:80px;top:30px;font-family:"Roboto",sans-serif;font-weight:500;font-size:15px}
.quote .stars{position:absolute;left:80px;top:52px}
.quote .mark{position:absolute;right:22px;top:34px}
.quote p{position:absolute;left:20px;right:20px;top:92px;font-family:"Roboto",sans-serif;font-style:italic;font-size:13.5px;line-height:25px;color:#666;text-align:justify}
.dots{position:absolute;left:1120px;top:252px;display:flex;flex-direction:column;gap:8px}
.dots i{width:11px;height:11px;border-radius:50%;background:#555;display:block}
.dots i.off{background:#fff;border:1.5px solid #555}

/* contact */
.contact{top:3938px;height:612px;background:var(--grey)}
.contact .h2{top:82px}
.corner{position:absolute;left:137px;top:162px;width:133px;height:95px;background:var(--green)}
.form{position:absolute;left:152px;top:177px;width:516px;height:405px;background:#fff}
.field{position:absolute;height:34px;border:1px solid #bbb;font-size:10px;padding:10px;color:#333}
.check{position:absolute;left:106px;top:324px;display:flex;align-items:center;gap:10px;font-size:10.5px;color:#333}
.check i{width:15px;height:15px;border:1px solid #777;display:block}
.form .btn{left:176px;top:359px;width:166px;height:37px;font-weight:500;font-size:14px}
.getin{position:absolute;left:725px;top:170px;font-size:34px;color:#1d1d1f;font-weight:500}
.info{position:absolute;left:725px;display:flex;gap:18px;font-size:15px;color:#222}
.info .ic{width:34px;height:34px;border-radius:50%;background:var(--blue);display:flex;align-items:center;justify-content:center;flex:none}
.info b{display:block;font-size:13px;font-weight:700;margin-bottom:6px}
.follow{position:absolute;left:725px;top:466px;font-size:15px;color:#333}
.social{position:absolute;top:502px;width:32px;height:32px;border-radius:50%;border:1.5px solid var(--blue);display:flex;align-items:center;justify-content:center}
.social i{width:10px;height:10px;border-radius:50%;background:var(--blue)}

/* footer */
.site-footer{top:4550px;height:400px;background:var(--navy);color:#fff}
.foot-brand{position:absolute;left:112px;top:102px;width:260px}
.foot-brand .brand-name{color:#fff;font-size:22px}
.col{position:absolute;top:78px}
.col h4{font-family:"Della Respira",serif;font-weight:400;font-size:19px;margin-bottom:20px}
.col li{list-style:none;font-size:15px;margin-bottom:21px;display:flex;gap:16px;align-items:center}
.col li::before{content:"»";color:var(--green);font-size:15px}
.fc{display:flex;gap:14px;margin-bottom:20px;font-size:13.5px;align-items:flex-start}
.fc .ic{width:28px;height:28px;display:flex;align-items:center;justify-content:center;flex:none;margin-top:10px}
.fc span{display:block;line-height:26px}
.foot-rule{position:absolute;left:112px;width:975px;top:316px;height:1px;background:#2a2f55}
.copy{position:absolute;left:0;width:1200px;top:356px;text-align:center;font-size:14px}
</style>
</head>
<body>

<header class="site-header">
  <div class="brand"><span class="brand-name">Northgate Bid Partners</span></div>
  <nav class="nav"><span>Home</span><span>Work with Us</span><span>Work for Us</span><span>About Us</span><span>Contact</span></nav>
  <div class="btn btn-blue login">LOGIN <span class="dot"></span></div>
</header>

<section class="hero">
  <div class="hero-photo" role="img" aria-label="Two engineers in hard hats reviewing a tablet on a factory floor"></div>
  <div class="hero-title">Generate Success</div>
  <div class="hero-sub">Fuel Innovation in Proposal Excellence with Northgate! Click here to explore our services.</div>
  <div class="btn btn-green">GET STARTED <span class="dot"></span></div>
</section>

<section class="what">
  <div class="h2">What We Do</div>
  <p class="lead" style="top:133px">Northgate Bid Partners, specializes in advancingan organization through a comprehensive suite of services designed to modernize the proposal development process. From innovative Capture Management strategies that pinpoint lucrative opportunities, meticulous Proposal Development services that transform concepts into effectivenarratives, and cutting-edge Generative AI techniques that create domain-aware content accelerating proposal draft development, we are your dedicated partner in securing success. With a unique fusion of technical expertise and exceptional writing capabilities, we surpass industry standards and set new benchmarks for excellence.</p>
  <p class="lead" style="top:332px">Discover a dynamic approach to proposal consulting that goes beyond conventional boundaries—choose Northgate for solutions that Enhance the quality of your work, Elevate your corporate advantage, and Expand your industrypresence</p>
  <div class="rule"></div>

  <div class="feature" style="left:102px">
    <div class="ico"><svg width="56" height="56" viewBox="0 0 56 56" fill="none" stroke="#fff" stroke-width="2.5"><rect x="10" y="6" width="36" height="30" rx="3"/><circle cx="28" cy="19" r="6"/><path d="M6 44h14l8 4 14-8"/></svg></div>
    <h3>Proposal Development</h3>
    <p>Transform your vision into winning proposals with our Proposal Development services. We specialize in persuasive narratives, clear technical solutions, and strategic pricing</p>
    <div class="more">READ MORE <i></i></div>
  </div>
  <div class="feature active" style="left:440px">
    <div class="ico"><svg width="56" height="56" viewBox="0 0 56 56" fill="none" stroke="#fff" stroke-width="2.5"><circle cx="28" cy="20" r="9"/><circle cx="28" cy="20" r="3"/><path d="M6 44h14l8 4 14-8M44 12h6M44 26h6"/></svg></div>
    <h3>Capture Management</h3>
    <p>Elevate your business development strategy with our Capture Management services. From opportunity identification to strategic planning, our experts will guide you through a</p>
    <div class="more">READ MORE <i></i></div>
  </div>
  <div class="feature" style="left:778px">
    <div class="ico"><svg width="56" height="56" viewBox="0 0 56 56" fill="none" stroke="#fff" stroke-width="2.5"><circle cx="28" cy="24" r="14"/><rect x="22" y="18" width="12" height="12"/><path d="M28 10V4M28 44v8M14 24H6M42 24h8"/></svg></div>
    <h3>Generative AI</h3>
    <p>Revolutionize your proposal writing process with our domain-aware Generative AI services. Using customer-installed tools, we leverage domain-aware artificial intelligence to generate</p>
    <div class="more">READ MORE <i></i></div>
  </div>
</section>

<section class="who">
  <div class="who-photo" role="img" aria-label="Two site workers in hard hats talking at an industrial facility"></div>
  <div class="who-title">Who We Are</div>
  <p class="who-text" style="top:125px">Lorem ipsum dolor sit amet, consectetur adipiscing elit, sed do eiusmod tempor incididunt ut labore et dolore magna aliqua. Ut enim ad minim veniam, quis nostrud exercitation ullamco laboris nisi ut aliquip ex ea commodo consequat. Duis aute irure dolor in reprehenderit in voluptate velit esse cillum dolore eu fugiat nulla pariatur. Excepteur sint occaecat cupidatat non proident, sunt in culpa qui officia deserunt mollit anim id est laborum</p>
  <p class="who-text" style="top:357px">perspiciatis unde omnis iste natus error sited voluptatem accusantium doloremque laudantium, totam rem aperiam, eaque ipsa quae ab illo inventore veritatised.</p>
  <div class="btn btn-green">LEARN MORE <span class="dot"></span></div>
</section>

<section class="services">
  <div class="h2">Our Services</div>
  <div class="arrow" style="left:39px"><svg width="10" height="14" viewBox="0 0 10 14" fill="none" stroke="#999" stroke-width="1.5"><path d="M8 1 2 7l6 6"/></svg></div>
  <div class="svc" style="left:94px"><div class="ico"><svg width="46" height="46" viewBox="0 0 46 46" fill="none" stroke="#fff" stroke-width="2.2"><circle cx="23" cy="18" r="9"/><circle cx="23" cy="18" r="3"/><path d="M6 36h12l6 3 12-6"/></svg></div><h3>Technical Solutioning</h3><p>Lorem ipsumed dolnor siteded ameteconsectetur adipiscing incididunt ute labore et dolore magna aliquat minimed.</p></div>
  <div class="svc active" style="left:347px"><div class="ico"><svg width="46" height="46" viewBox="0 0 46 46" fill="none" stroke="#0b1b3a" stroke-width="2.2"><rect x="10" y="6" width="22" height="30" rx="2"/><path d="M15 14h12M15 20h12M15 26h8"/><circle cx="34" cy="34" r="6"/></svg></div><h3>Capture Management</h3><p>Lorem ipsumed dolnor siteded ameteconsectetur adipiscing incididunt ute labore et dolore magna aliquat minimed.</p></div>
  <div class="svc" style="left:600px"><div class="ico"><svg width="46" height="46" viewBox="0 0 46 46" fill="none" stroke="#fff" stroke-width="2.2"><rect x="12" y="6" width="22" height="24" rx="2"/><path d="M17 13h12M17 19h12"/><path d="M6 38h12l6 3 12-6"/></svg></div><h3>Proposal Management</h3><p>Lorem ipsumed dolnor siteded ameteconsectetur adipiscing incididunt ute labore et dolore magna aliquat minimed.</p></div>
  <div class="svc" style="left:852px"><div class="ico"><svg width="50" height="50" viewBox="0 0 50 50" fill="none" stroke="#fff" stroke-width="2.2"><circle cx="25" cy="25" r="12"/><path d="M25 6v7M25 37v7M6 25h7M37 25h7"/><text x="25" y="29" text-anchor="middle" font-family="Roboto,sans-serif" font-size="10" fill="#fff" stroke="none">AI</text></svg></div><h3>Generative AI</h3><p>Lorem ipsumed dolnor siteded ameteconsectetur adipiscing incididunt ute labore et dolore magna aliquat minimed.</p></div>
  <div class="arrow" style="left:1123px"><svg width="10" height="14" viewBox="0 0 10 14" fill="none" stroke="#999" stroke-width="1.5"><path d="M2 1l6 6-6 6"/></svg></div>
</section>

<section class="sme">
  <div class="h2">Subject Matter Expertise</div>
  <div class="topic" style="left:96px"><div class="pic" role="img" aria-label="Humanoid robot head" style="background:radial-gradient(circle,#5d6c85,#1c2434)"></div>Generative AI</div>
  <div class="topic" style="left:298px"><div class="pic" role="img" aria-label="Technician assembling hardware at a workbench" style="background:radial-gradient(circle,#c9c2b6,#6e6a63)"></div>Software/ Hardware<br>Engineering</div>
  <div class="topic" style="left:500px"><div class="pic" role="img" aria-label="Engineer working at multiple monitors" style="background:radial-gradient(circle,#8fa5c0,#2f3d52)"></div>Systems Engineering</div>
  <div class="topic" style="left:700px"><div class="pic" role="img" aria-label="Cloud computing network concept" style="background:radial-gradient(circle,#d9d4cc,#44484f)"></div>High-Performance<br>Computing</div>
  <div class="topic" style="left:902px"><div class="pic" role="img" aria-label="Delivery van loaded with parcels" style="background:radial-gradient(circle,#b58a5a,#2b2f3a)"></div>Logistics</div>
  <div class="btn btn-green">VIEW MORE <span class="dot"></span></div>
</section>

<section class="testi">
  <div class="h2">Our Testimonials</div>
  <div class="quote" style="left:94px">
    <div class="avatar" role="img" aria-label="Client portrait"></div>
    <div class="name">Jhon Deo</div>
    <svg class="stars" width="74" height="12" viewBox="0 0 74 12" fill="#1ff0bd"><g id="s"><path d="M6 0l1.8 3.9 4.2.4-3.2 2.8 1 4.1L6 9 2.2 11.2l1-4.1L0 4.3l4.2-.4z"/></g><use href="#s" x="15"/><use href="#s" x="30"/><use href="#s" x="45"/><use href="#s" x="60"/></svg>
    <svg class="mark" width="30" height="22" viewBox="0 0 30 22" fill="#1ff0bd"><path d="M0 22V12C0 5 4 1 11 0v5c-3 1-5 3-5 7h5v10zM17 22V12c0-7 4-11 11-12v5c-3 1-5 3-5 7h5v10z"/></svg>
    <p>perspiciatis unde omnis iste natus error sit voluptatem accusantium dolorlaudantium, periam, eaque ipsa quae ab illo inventore veritatis et quasi architecto beatae vitae dicta sunt explicabo. Nemo enim ipsam voluptatem quia voluptas sit</p>
  </div>
  <div class="quote" style="left:435px">
    <div class="avatar" role="img" aria-label="Client portrait"></div>
    <div class="name">Jhon Deo</div>
    <svg class="stars" width="74" height="12" viewBox="0 0 74 12" fill="#1ff0bd"><use href="#s"/><use href="#s" x="15"/><use href="#s" x="30"/><use href="#s" x="45"/><use href="#s" x="60"/></svg>
    <svg class="mark" width="30" height="22" viewBox="0 0 30 22" fill="#1ff0bd"><path d="M0 22V12C0 5 4 1 11 0v5c-3 1-5 3-5 7h5v10zM17 22V12c0-7 4-11 11-12v5c-3 1-5 3-5 7h5v10z"/></svg>
    <p>perspiciatis unde omnis iste natus error sit voluptatem accusantium dolorlaudantium, periam, eaque ipsa quae ab illo inventore veritatis et quasi architecto beatae vitae dicta sunt explicabo. Nemo enim ipsam voluptatem quia voluptas sit</p>
  </div>
  <div class="quote" style="left:775px">
    <div class="avatar" role="img" aria-label="Client portrait"></div>
    <div class="name">Jhon Deo</div>
    <svg class="stars" width="74" height="12" viewBox="0 0 74 12" fill="#1ff0bd"><use href="#s"/><use href="#s" x="15"/><use href="#s" x="30"/><use href="#s" x="45"/><use href="#s" x="60"/></svg>
    <svg class="mark" width="30" height="22" viewBox="0 0 30 22" fill="#1ff0bd"><path d="M0 22V12C0 5 4 1 11 0v5c-3 1-5 3-5 7h5v10zM17 22V12c0-7 4-11 11-12v5c-3 1-5 3-5 7h5v10z"/></svg>
    <p>perspiciatis unde omnis iste natus error sit voluptatem accusantium dolorlaudantium, periam, eaque ipsa quae ab illo inventore veritatis et quasi architecto beatae vitae dicta sunt explicabo. Nemo enim ipsam voluptatem quia voluptas sit</p>
  </div>
  <div class="dots"><i></i><i></i><i class="off"></i><i></i></div>
</section>

<section class="contact">
  <div class="h2">Contact Us</div>
  <div class="corner"></div>
  <div class="form">
    <div class="field" style="left:38px;top:60px;width:212px">First Name:</div>
    <div class="field" style="left:266px;top:60px;width:212px">Email:</div>
    <div class="field" style="left:38px;top:113px;width:212px">Phone Number:</div>
    <div class="field" style="left:266px;top:113px;width:212px">Address:</div>
    <div class="field" style="left:38px;top:165px;width:440px;height:70px">Message:</div>
    <div class="check"><i></i>perspiciatis unde omnis iste natus error sit voluptatem a</div>
    <div class="btn btn-blue">SUBMIT NOW <span class="dot"></span></div>
  </div>
  <div class="getin">Get In Touch With Us</div>
  <div class="info" style="top:243px"><span class="ic"><svg width="16" height="16" viewBox="0 0 24 24" fill="#fff"><path d="M6.6 10.8a15 15 0 0 0 6.6 6.6l2.2-2.2c.3-.3.7-.4 1-.2 1.1.4 2.3.6 3.6.6.6 0 1 .4 1 1V20c0 .6-.4 1-1 1A17 17 0 0 1 3 4c0-.6.4-1 1-1h3.5c.6 0 1 .4 1 1 0 1.3.2 2.5.6 3.6.1.3 0 .7-.2 1z"/></svg></span><div><b>Phone Number :</b>(555) 014-2280</div></div>
  <div class="info" style="top:308px"><span class="ic"><svg width="16" height="16" viewBox="0 0 24 24" fill="#fff"><path d="M2 5h20v14H2zm2 2v.5l8 5 8-5V7z"/></svg></span><div><b>Email :</b>info@northgatebid.com</div></div>
  <div class="info" style="top:378px"><span class="ic"><svg width="14" height="16" viewBox="0 0 24 24" fill="#fff"><path d="M12 2a7 7 0 0 0-7 7c0 5 7 13 7 13s7-8 7-13a7 7 0 0 0-7-7zm0 9.5A2.5 2.5 0 1 1 12 6.5a2.5 2.5 0 0 1 0 5z"/></svg></span><div><b>Address :</b>412 SLorem ipsum dolor sit amet632</div></div>
  <div class="follow">Follow Us</div>
  <div class="social" style="left:719px"><i></i></div>
  <div class="social" style="left:763px"><i></i></div>
  <div class="social" style="left:807px"><i></i></div>
</section>

<footer class="site-footer">
  <div class="foot-brand"><div class="brand-name">Northgate Bid Partners</div></div>
  <div class="col" style="left:432px"><h4>Quick links</h4><ul><li>Home</li><li>Work with Us</li><li>Work for Us</li><li>About Us</li><li>Contact</li></ul></div>
  <div class="col" style="left:645px"><h4>Other links</h4><ul><li>Terms of Use</li><li>Terms &amp; Condition</li><li>News</li><li>Privacy Policy</li><li>FAQ</li></ul></div>
  <div class="col" style="left:886px"><h4 style="font-size:17px">Contact Us</h4>
    <div class="fc"><span class="ic"><svg width="16" height="16" viewBox="0 0 24 24" fill="#1ff0bd"><path d="M6.6 10.8a15 15 0 0 0 6.6 6.6l2.2-2.2c.3-.3.7-.4 1-.2 1.1.4 2.3.6 3.6.6.6 0 1 .4 1 1V20c0 .6-.4 1-1 1A17 17 0 0 1 3 4c0-.6.4-1 1-1h3.5c.6 0 1 .4 1 1 0 1.3.2 2.5.6 3.6.1.3 0 .7-.2 1z"/></svg></span><div><span>Phone</span><span>(555) 014-2280</span></div></div>
    <div class="fc"><span class="ic"><svg width="16" height="16" viewBox="0 0 24 24" fill="#1ff0bd"><path d="M2 5h20v14H2zm2 2v.5l8 5 8-5V7z"/></svg></span><div><span>Email</span><span>info@northgatebid.com</span></div></div>
  </div>
  <div class="foot-rule"></div>
  <div class="copy">© 2023 Northgate Bid Partners. All right reserved.</div>
</footer>

</body>
</html>
```